Executive Coaching Consultancy Website Design

I am setting up an executive coaching consultancy practice, primarily targeting ambitious women (and men of course!) who want to progress to the next level in their careers (late 20's to mid forties in age) or who are returning to work after a career break. I need a simple website that promotes the benefits of my consultancy service, contact details plus other associated information and incorporates social media channels so I can update information and news items on a regular basis. It would be useful to have a design for a Corvamesh dedicated page too.

This project has been on the back burner for a while due to other commitments, however when I originally decided to set the business up a couple of years ago, I did get a logo and some illustrations for the website designed and produced - which I've uploaded.

The design should convey expertise, understanding, serenity and trust. I am keen it appears stylish and different to many of the other coaching websites that use typical business imagery and are very cluttered. I am targeting individuals who want to invest their own time and money into getting to the next step (as opposed to targeting HR teams in large organisations).

The design should also be responsive so the target audience can easily view it on their phones/tablets.

Initially the information to be conveyed on the website will include:

- How coaching can improve career performance
- The coaching process and what to expect
- Fees
- About us
- Contact details
- A Blog
- Links to useful articles/organisations

etc.

A simple scroll down format would make sense but I will leave it to your best judgement!

Many thanks!!

Reason: Realised it was still the holiday period but am keen to receive prospective designs so I can commission this project quickly. Thanks!

Target Market(s)

28-45 yr old career women

Industry/Entity Type

Business

Number of Pages Required

2 page

Requirements
Must have
• Clean, simple intuitive navigation that can be adapted easily for responsive design purposes
Nice to have
• Area for testimonials
Should not have
• Cluttered information.

```html
<!DOCTYPE html>
<html lang="en">
<head>
<meta charset="utf-8">
<title>Halden Marsh – Executive Coaching Consultancy</title>
<link rel="stylesheet" href="https://fonts.googleapis.com/css2?family=Oswald:wght@400&family=Ubuntu:wght@300;400&family=Open+Sans:wght@400;600;700&display=swap">
<style>
  :root {
    --teal: #2aa3a5;
    --teal-dark: #1e7f81;
    --cyan-band: #2ecbcf;
    --heading-teal: #2aa3a5;
    --text: #6b6b6b;
    --text-dark: #555555;
    --white: #ffffff;
    --footer-bg: #333333;
    --footer-text: #c9c9c9;
    --footer-rule: #4a4a4a;
    --badge: #2a72b5;
  }
  * { box-sizing: border-box; margin: 0; padding: 0; }
  html, body { width: 1200px; height: 2164px; overflow: hidden; }
  body { font-family: "Open Sans", Arial, sans-serif; color: var(--text); background: var(--white); position: relative; }

  .btn {
    display: inline-block; background: var(--teal); color: var(--white);
    font-family: "Open Sans", Arial, sans-serif; font-weight: 600;
    border-bottom: 3px solid var(--teal-dark); border-radius: 3px; text-decoration: none;
  }

  /* Header */
  .site-header { position: absolute; top: 0; left: 0; width: 1200px; height: 67px; background: var(--teal); z-index: 3; }
  .brand {
    position: absolute; left: 125px; top: 0; width: 179px; height: 133px; background: var(--white);
    display: flex; align-items: center; justify-content: center;
    box-shadow: 0 1px 3px rgba(0,0,0,.2);
  }
  .brand-name { font-weight: 600; color: var(--text-dark); font-size: 20px; }
  .main-nav { position: absolute; right: 126px; top: 22px; display: flex; gap: 26px; }
  .main-nav a { color: var(--white); text-decoration: none; font-size: 14.5px; }

  /* Hero */
  .hero { position: absolute; top: 0; left: 0; width: 1200px; height: 646px; }
  .hero-photo { position: absolute; inset: 0; background: linear-gradient(100deg, #7d8084 0%, #b3b5b7 40%, #c7c8c9 60%, #85888b 100%); }
  .hero-copy { position: absolute; top: 245px; left: 0; width: 1200px; text-align: center; color: var(--white); }
  .hero-title { font-family: "Oswald", "Arial Narrow", sans-serif; font-weight: 400; font-size: 60px; line-height: 72px; }
  .hero-text { font-size: 13.5px; font-weight: 600; line-height: 20px; width: 520px; margin: 14px auto 0; }
  .hero .btn { margin-top: 22px; font-size: 16px; padding: 7px 18px; }

  /* Welcome */
  .welcome { position: absolute; top: 646px; left: 0; width: 1200px; height: 216px; text-align: center; }
  .welcome h2 { font-family: "Ubuntu", sans-serif; font-weight: 400; color: var(--heading-teal); font-size: 27px; margin-top: 20px; }
  .welcome p { width: 850px; margin: 14px auto 0; font-size: 13.2px; line-height: 20.5px; }
  .welcome .btn { margin-top: 16px; font-size: 15.5px; padding: 7px 20px; }

  /* Services */
  .services { position: absolute; top: 862px; left: 0; width: 1200px; height: 471px; background: var(--cyan-band); }
  .service-list { position: absolute; top: 38px; left: 125px; display: flex; gap: 26px; }
  .service-card {
    width: 300px; height: 397px; background: var(--white); border-radius: 3px;
    border-bottom: 4px solid #4a4a4a; overflow: hidden;
  }
  .service-photo { height: 239px; border-bottom: 3px solid var(--teal); }
  .photo-desk { background: linear-gradient(135deg, #e9eef2, #c9d3da); }
  .photo-team { background: linear-gradient(135deg, #c77a4a, #3a6a8a 55%, #e2d6c8); }
  .photo-laptop { background: linear-gradient(135deg, #b3a89a, #6e7a88 60%, #3b4c66); }
  .service-body { padding: 14px 15px 0; }
  .service-body h3 { font-size: 16.5px; font-weight: 600; color: var(--text-dark); }
  .service-sub { font-size: 14px; margin-top: 4px; }
  .service-text { font-size: 12.8px; line-height: 20.5px; margin-top: 10px; text-align: justify; }

  /* News */
  .news { position: absolute; top: 1333px; left: 0; width: 1200px; height: 317px; }
  .news h2 { font-family: "Ubuntu", sans-serif; font-weight: 300; color: var(--heading-teal); font-size: 35px; position: absolute; left: 124px; top: 22px; }
  .news-list { position: absolute; top: 84px; left: 125px; display: flex; gap: 26px; }
  .news-item { width: 300px; }
  .news-item h3 { font-size: 15.5px; font-weight: 600; color: var(--text-dark); white-space: nowrap; }
  .news-date { display: flex; align-items: center; gap: 4px; font-size: 12.5px; margin-top: 5px; }
  .share-badge { width: 15px; height: 15px; background: var(--badge); display: inline-block; }
  .news-text { font-size: 12.4px; line-height: 20.5px; margin-top: 12px; text-align: justify; }
  .news-item .btn { margin-top: 8px; font-size: 13px; padding: 3px 10px; }

  /* Contact */
  .contact { position: absolute; top: 1650px; left: 0; width: 1200px; height: 234px; }
  .contact-photo { position: absolute; inset: 0; background: linear-gradient(90deg, #4b4b4b, #5e5e5e 50%, #4e4e4e); }
  .contact h2 { position: absolute; top: 16px; width: 1200px; text-align: center; color: var(--white); font-weight: 400; font-size: 35px; }
  .contact-form { position: absolute; top: 83px; left: 125px; width: 950px; height: 110px; }
  .field { position: absolute; top: 0; height: 49px; background: var(--white); padding: 0 16px; font-size: 18px; font-weight: 600; color: #666; display: flex; align-items: center; }
  .field-name { left: 0; width: 243px; }
  .field-email { left: 262px; width: 243px; }
  .field-message { left: 521px; width: 429px; }
  .send-btn { position: absolute; left: 776px; top: 64px; width: 173px; height: 45px; border: 1.5px solid var(--white); border-radius: 3px; color: var(--white); font-size: 18px; font-weight: 600; display: flex; align-items: center; justify-content: center; }

  /* Footer */
  .site-footer { position: absolute; top: 1884px; left: 0; width: 1200px; height: 280px; background: var(--footer-bg); color: var(--footer-text); }
  .footer-col { position: absolute; top: 36px; width: 200px; }
  .footer-col h4 { color: var(--white); font-size: 17px; font-weight: 600; padding-bottom: 4px; border-bottom: 1px solid var(--footer-rule); width: 137px; }
  .col-articles { left: 126px; }
  .col-news { left: 372px; }
  .col-contact { left: 614px; }
  .col-social { left: 859px; }
  .article-list { list-style: none; margin-top: 9px; }
  .article-list li { font-size: 13.5px; line-height: 20.7px; }
  .article-list li::before { content: "»"; margin-right: 6px; }
  .news-blurb { font-size: 10.5px; line-height: 16px; margin-top: 9px; width: 176px; }
  .news-input { width: 178px; height: 24px; background: var(--white); color: #888; font-size: 10.5px; padding: 4px 6px; margin-top: 10px; }
  .news-input + .news-input { margin-top: 11px; }
  .subscribe { display: inline-block; background: var(--teal); color: var(--white); font-size: 10.5px; padding: 4px 17px; margin-top: 16px; }
  .contact-lines { list-style: none; margin-top: 9px; }
  .contact-lines li { display: flex; gap: 8px; font-size: 13.5px; line-height: 20.5px; margin-bottom: 7px; }
  .contact-lines svg { flex: none; margin-top: 5px; }
  .social-list { list-style: none; margin-top: 9px; }
  .social-list li { display: flex; align-items: center; gap: 9px; font-size: 13.5px; color: var(--white); margin-bottom: 8px; }
  .social-square { width: 22px; height: 22px; background: #555; display: inline-block; }
</style>
</head>
<body>
  <section class="hero">
    <div class="hero-photo" role="img" aria-label="Photo of a coach presenting at a whiteboard to a seated group of professionals"></div>
    <div class="hero-copy">
      <h1 class="hero-title">Executive Coaching Consultancy</h1>
      <p class="hero-text">Lorem Ipsum is simply dummy text of the printing and typesetting industry. Lorem Ipsum has been the industry's standard dummy text ever since thewhen an unknown</p>
      <a class="btn" href="#">Know More</a>
    </div>
  </section>

  <header class="site-header">
    <div class="brand">
      <span class="brand-name">Halden Marsh</span>
    </div>
    <nav class="main-nav">
      <a href="#">Home</a><a href="#">About Us</a><a href="#">What We Do</a><a href="#">Fees</a><a href="#">Blogs</a><a href="#">Links</a><a href="#">Contact Us</a>
    </nav>
  </header>

  <section class="welcome">
    <h2>Welcome to Halden Marsh</h2>
    <p>Lorem ipsum dolor sit amet, consectetuer adipiscing elit. Praesent vestibulum molestie lacus. Aenean nonummy hendrerit mauris. Phasellus porta. Fusce suscipit varius mi. Lorem ipsum dolor sit amet, consectetuer adipiscing elit. Praesent vestibulum molestie lacus. Aenean nonummy hendrerit mauris.</p>
    <a class="btn" href="#">Read More</a>
  </section>

  <section class="services">
    <div class="service-list">
      <article class="service-card">
        <div class="service-photo photo-desk" role="img" aria-label="Photo of a woman working at a laptop in a bright office"></div>
        <div class="service-body">
          <h3>Lorem Ipsum is simply dummy</h3>
          <p class="service-sub">Consectetuer adipiscing elit.</p>
          <p class="service-text">Lorem ipsum dolor sit amet, consec tetuer adipiscing elit. Praesent vestibulum molestie lacus.</p>
        </div>
      </article>
      <article class="service-card">
        <div class="service-photo photo-team" role="img" aria-label="Photo of a group of colleagues gathered around a laptop"></div>
        <div class="service-body">
          <h3>Lorem Ipsum is simply dummy</h3>
          <p class="service-sub">Consectetuer adipiscing elit.</p>
          <p class="service-text">Lorem ipsum dolor sit amet, consec tetuer adipiscing elit. Praesent vestibulum molestie lacus.</p>
        </div>
      </article>
      <article class="service-card">
        <div class="service-photo photo-laptop" role="img" aria-label="Photo of hands typing on a laptop beside a phone"></div>
        <div class="service-body">
          <h3>Lorem Ipsum is simply dummy</h3>
          <p class="service-sub">Consectetuer adipiscing elit.</p>
          <p class="service-text">Lorem ipsum dolor sit amet, consec tetuer adipiscing elit. Praesent vestibulum molestie lacus.</p>
        </div>
      </article>
    </div>
  </section>

  <section class="news">
    <h2>Recent News</h2>
    <div class="news-list">
      <article class="news-item">
        <h3>Lorem ipsum dolor sit amet consectet</h3>
        <p class="news-date">27 FEB 2014 <span class="share-badge" aria-label="Share on Corvamesh"></span></p>
        <p class="news-text">Sed do eiusmod tempor incididunt ut labore et dolore magna aliqua. Ut enim ad minim veniam, quis nostrud exercitation ullamco laboris nisi ut aliquip ex ea commodo consequat</p>
        <a class="btn" href="#">Read More</a>
      </article>
      <article class="news-item">
        <h3>Lorem ipsum dolor sit amet, consect</h3>
        <p class="news-date">27 FEB 2014 <span class="share-badge" aria-label="Share on Corvamesh"></span></p>
        <p class="news-text">Sed do eiusmod tempor incididunt ut labore et dolore magna aliqua. Ut enim ad minim veniam, quis nostrud exercitation ullamco laboris nisi ut aliquip ex ea commodo consequat</p>
        <a class="btn" href="#">Read More</a>
      </article>
      <article class="news-item">
        <h3>Lorem ipsum dolor sit amet, consect</h3>
        <p class="news-date">27 FEB 2014 <span class="share-badge" aria-label="Share on Corvamesh"></span></p>
        <p class="news-text">Sed do eiusmod tempor incididunt ut labore et dolore magna aliqua. Ut enim ad minim veniam, quis nostrud exercitation ullamco laboris nisi ut aliquip ex ea commodo consequat</p>
        <a class="btn" href="#">Read More</a>
      </article>
    </div>
  </section>

  <section class="contact">
    <div class="contact-photo" role="img" aria-label="Dark photo of a desk with a monitor and a coffee cup"></div>
    <h2>Contact Us</h2>
    <div class="contact-form">
      <div class="field field-name">Name</div>
      <div class="field field-email">Email</div>
      <div class="field field-message">Message</div>
      <div class="send-btn">Send Message</div>
    </div>
  </section>

  <footer class="site-footer">
    <div class="footer-col col-articles">
      <h4>Articles</h4>
      <ul class="article-list">
        <li>lorem ipsum</li><li>ipsum lorem</li><li>lorem ipsum</li><li>lorem ipsum</li><li>lorem ipsum</li><li>lorem ipsum</li><li>lorem ipsum</li>
      </ul>
    </div>
    <div class="footer-col col-news">
      <h4>NewsLatters</h4>
      <p class="news-blurb">It is a long established fact that a reader will be distracted by the</p>
      <div class="news-input">Your Name</div>
      <div class="news-input">Your Email</div>
      <span class="subscribe">Subscibe</span>
    </div>
    <div class="footer-col col-contact">
      <h4>Contact Us</h4>
      <ul class="contact-lines">
        <li><svg width="10" height="12" viewBox="0 0 10 12"><path d="M5 0a4 4 0 0 0-4 4c0 3 4 8 4 8s4-5 4-8a4 4 0 0 0-4-4zm0 5.5A1.5 1.5 0 1 1 5 2.5a1.5 1.5 0 0 1 0 3z" fill="#fff"/></svg><span>418 Linden Row Suite 4<br>Marbury Park<br>7301</span></li>
        <li><svg width="11" height="11" viewBox="0 0 11 11"><path d="M2.2 0.5l2 2-1.2 1.5c.8 1.6 2 2.8 3.6 3.6L8 6.4l2 2-1.4 2C4.5 10.2.6 6.3.3 1.9z" fill="#fff"/></svg><span>5550 2568 0199</span></li>
        <li><svg width="12" height="9" viewBox="0 0 12 9"><rect width="12" height="9" fill="#fff"/><path d="M0 0l6 5 6-5" stroke="#333" fill="none"/></svg><span>hello@haldenmarsh.com</span></li>
      </ul>
    </div>
    <div class="footer-col col-social">
      <h4>Follows Us</h4>
      <ul class="social-list">
        <li><span class="social-square"></span>Gatherly</li>
        <li><span class="social-square"></span>Quipster</li>
        <li><span class="social-square"></span>Orbitly</li>
        <li><span class="social-square"></span>Reelcast</li>
      </ul>
    </div>
  </footer>
</body>
</html>
```